Thornbury Building Company - Card Design

I am looking to use the logo designs that you already did for me to develop a business card. I would like the card to have a black background and be double sided. I want white and green logo and text. I have attached an inspiration photo of a look that I like. I would like to use the Vertical Logo attached to take up the full front side of the card. On the back where I have my name and information, I would like to have the horizontal logo or maybe even just the image of the 'A' and trees without the text. I am open, but I am looking for something clean and simple and I want the green to really pop! Additional files can be found under Design #: 58302946

Target Market(s)

Homeowners

Industry/Entity Type

Construction

Contact Information for Business Card

Name: Marcus Thornbury, Title: Project Manager, Phone: 555.274.8136, Email: thornburybuildingcompany@mailvesta.com, address: 487 Larkspur Ln, Alder Springs, CA 95033, Lic# 2468317

Colors
00AB8E
00BBA5
67D7C9
C6EFE9
E9F9F6

Requirements
Nice to have
• I would like to see the logos that I have already got from ArtLoomHub, though I am open to new ones

```html
<!DOCTYPE html>
<html lang="en">
<head>
<meta charset="utf-8">
<title>Thornbury Building Company – Business Card</title>
<link href="https://fonts.googleapis.com/css2?family=Arimo:wght@400;700&display=swap" rel="stylesheet">
<style>
  :root {
    --backdrop: #262626;
    --card: #1b1b1b;
    --green: #6cb94a;
    --white: #ffffff;
    --font: "Arimo", Arial, sans-serif;
  }
  html, body {
    margin: 0;
    padding: 0;
    width: 1200px;
    height: 988px;
    overflow: hidden;
    background: var(--backdrop);
    font-family: var(--font);
  }
  .sheet {
    width: 1200px;
    height: 988px;
    display: flex;
    flex-direction: column;
    align-items: center;
    justify-content: center;
    gap: 40px;
  }
  .card {
    position: relative;
    width: 760px;
    height: 434px;
    background: var(--card);
    border-radius: 26px;
    overflow: hidden;
    box-shadow: 0 10px 30px rgba(0,0,0,0.55);
  }

  .brand {
    display: flex;
    align-items: center;
    gap: 14px;
    color: var(--white);
    font-weight: 700;
    text-transform: uppercase;
    letter-spacing: 2px;
    white-space: nowrap;
  }
  .brand-square {
    background: var(--green);
    flex: none;
  }

  .card-front .brand {
    position: absolute;
    left: 50%;
    top: 50%;
    transform: translate(-50%, -50%);
    font-size: 34px;
  }
  .card-front .brand-square { width: 40px; height: 40px; }

  .card-back .brand {
    position: absolute;
    left: 200px;
    top: 78px;
    font-size: 26px;
  }
  .card-back .brand-square { width: 30px; height: 30px; }

  .person {
    position: absolute;
    right: 420px;
    top: 196px;
    text-align right;
    text-align: right;
  }
  .person-name {
    margin: 0;
    color: var(--green);
    font-weight: 700;
    font-size: 27px;
    letter-spacing: 0.5px;
    text-transform: uppercase;
    white-space: nowrap;
  }
  .person-title {
    margin: 4px 0 0;
    color: var(--white);
    font-size: 17px;
  }
  .divider {
    position: absolute;
    left: 362px;
    top: 170px;
    width: 1.5px;
    height: 90px;
    background: var(--green);
  }
  .contact {
    position: absolute;
    left: 384px;
    top: 166px;
    margin: 0;
    padding: 0;
    list-style: none;
    font-size: 16px;
    color: var(--white);
  }
  .contact li {
    display: flex;
    align-items: center;
    gap: 8px;
    height: 30px;
    white-space: nowrap;
  }
  .contact .license { color: var(--green); }
  .contact svg { width: 14px; height: 14px; fill: var(--green); flex: none; }

  .address-band {
    position: absolute;
    left: 0;
    right: 0;
    top: 302px;
    height: 50px;
    background: var(--green);
    color: var(--white);
    font-size: 18px;
    display: flex;
    align-items: center;
    justify-content: center;
    white-space: nowrap;
  }
</style>
</head>
<body>
<main class="sheet">
  <section class="card card-front" aria-label="Card front">
    <div class="brand">
      <span class="brand-square"></span>
      <span class="brand-name">Thornbury Building Company</span>
    </div>
  </section>

  <section class="card card-back" aria-label="Card back">
    <div class="brand">
      <span class="brand-square"></span>
      <span class="brand-name">Thornbury Building Company</span>
    </div>

    <div class="person">
      <p class="person-name">Marcus Thornbury</p>
      <p class="person-title">Project Manager</p>
    </div>

    <div class="divider"></div>

    <ul class="contact">
      <li class="license">Lic# 2468317</li>
      <li>
        <svg viewBox="0 0 24 24" aria-hidden="true"><path d="M6.6 10.8a15.1 15.1 0 0 0 6.6 6.6l2.2-2.2a1 1 0 0 1 1-.25 11.4 11.4 0 0 0 3.6.57 1 1 0 0 1 1 1V20a1 1 0 0 1-1 1A17 17 0 0 1 3 4a1 1 0 0 1 1-1h3.5a1 1 0 0 1 1 1c0 1.25.2 2.45.57 3.57a1 1 0 0 1-.25 1z"/></svg>
        555.274.8136
      </li>
      <li>
        <svg viewBox="0 0 24 24" aria-hidden="true"><path d="M2 5h20v14H2z M2 5l10 8 10-8" /></svg>
        thornburybuildingcompany@mailvesta.com
      </li>
    </ul>

    <div class="address-band">487 Larkspur Ln, Alder Springs, CA 95033</div>
  </section>
</main>
</body>
</html>
```